BuildLinkHub.com Full Stationery Design

Business Card will have all info on it. Letterhead will not have name, title or mobile number. Keep general feeling very clean, using colors from the logo as accents.
Name:Dale Marchetti
Title:President
Phone: 1-800-555-0142
Cell: 306-555-0187
email: dale@buildlinkhub.example
website: www.buildlinkhub.example
Address:
PO Box 947
Cedarvale, PV
S0J2T0

Target Market(s)

Construction Business owners

Industry/Entity Type

Business

Contact Information for Business Card

Name:Dale Marchetti
Title:President
Phone: 1-800-555-0142
Cell: 306-555-0187
Address:
PO Box 947
Cedarvale, PV
S0J2T0

Font styles to use
Sans Serif

Requirements
Must have
• Clean look
Should not have
• Images or cartoon type characters or tools

```html
<!DOCTYPE html>
<html lang="en">
<head>
<meta charset="utf-8">
<title>BuildLinkHub.com Business Card</title>
<link rel="stylesheet" href="https://fonts.googleapis.com/css2?family=Source+Sans+3:wght@400;600;700&display=swap">
<style>
  :root {
    --backdrop: #5b4a3b;
    --paper: #ffffff;
    --slate: #4a5767;
    --slate-text: #4d5868;
    --ink: #5a5f66;
    --accent: #e8492a;
  }
  * { margin: 0; padding: 0; box-sizing: border-box; }
  html, body { width: 1200px; height: 987px; overflow: hidden; }
  body {
    position: relative;
    background: var(--backdrop);
    font-family: "Source Sans 3", Arial, sans-serif;
  }
  .card {
    position: absolute;
    left: 293px;
    width: 615px;
    height: 352px;
    box-shadow: 0 2px 6px rgba(0,0,0,0.35);
  }
  .card-front { top: 130px; background: var(--paper); }
  .card-back { top: 506px; background: var(--slate); }

  .brand {
    position: absolute;
    left: 46px;
    top: 50px;
    display: flex;
    align-items: center;
    gap: 12px;
  }
  .brand-square { width: 26px; height: 26px; background: var(--accent); }
  .brand-name {
    font-weight: 700;
    font-size: 32px;
    color: var(--slate-text);
    letter-spacing: 0.2px;
  }

  .contact {
    position: absolute;
    left: 46px;
    top: 174px;
    list-style: none;
    font-size: 15.5px;
    color: var(--ink);
    line-height: 23px;
  }
  .contact li { display: flex; align-items: center; gap: 8px; }
  .contact .gap { margin-top: 4px; }
  .contact svg { width: 14px; height: 14px; fill: var(--ink); flex: none; }

  .person {
    position: absolute;
    right: 49px;
    top: 210px;
    text-align: right;
  }
  .person-name { font-weight: 600; font-size: 22px; color: var(--slate-text); line-height: 26px; }
  .person-title { font-size: 16.5px; color: var(--accent); line-height: 22px; }

  .band { position: absolute; left: 0; bottom: 0; width: 615px; height: 36px; }
  .band-url {
    position: absolute;
    right: 18px;
    bottom: 10px;
    font-size: 16.5px;
    color: #ffffff;
  }

  .back-brand {
    position: absolute;
    right: 44px;
    top: 264px;
    text-align: left;
    color: #ffffff;
  }
  .back-brand-name { font-weight: 700; font-size: 40px; line-height: 44px; }
  .back-brand-url { font-size: 16.5px; line-height: 20px; }
</style>
</head>
<body>
  <section class="card card-front" aria-label="Business card front">
    <div class="brand">
      <span class="brand-square"></span>
      <span class="brand-name">BuildLinkHub.com</span>
    </div>

    <ul class="contact">
      <li>PO Box 947</li>
      <li>Cedarvale, PV, S0J2T0</li>
      <li class="gap">
        <svg viewBox="0 0 16 16" aria-hidden="true"><path d="M3.6 1.2l2.3 2.6-1.3 1.8c.9 2.1 2.6 3.8 4.7 4.7l1.8-1.3 2.6 2.3-1.4 2.2C7.4 14.9 1.1 8.6 1.4 2.6z"/></svg>
        1-800-555-0142
      </li>
      <li>
        <svg viewBox="0 0 16 16" aria-hidden="true"><path d="M4 0h8a1 1 0 0 1 1 1v14a1 1 0 0 1-1 1H4a1 1 0 0 1-1-1V1a1 1 0 0 1 1-1zm1 2v10h6V2zm3 11a1 1 0 1 0 0 2 1 1 0 0 0 0-2z"/></svg>
        306-555-0187
      </li>
      <li>
        <svg viewBox="0 0 16 16" aria-hidden="true"><path d="M1 3h14v10H1zm1.5 1.2L8 8.3l5.5-4.1z"/></svg>
        dale@buildlinkhub.example
      </li>
    </ul>

    <div class="person">
      <div class="person-name">Dale Marchetti</div>
      <div class="person-title">President</div>
    </div>

    <svg class="band" viewBox="0 0 615 36" aria-hidden="true">
      <rect x="0" y="12" width="615" height="17" fill="var(--slate)"/>
      <path d="M345 29 C358 29 360 0 375 0 L615 0 L615 29 Z" fill="var(--accent)"/>
      <path d="M343 29 C356 29 358 2 373 2" fill="none" stroke="#ffffff" stroke-width="2"/>
      <rect x="0" y="29" width="615" height="7" fill="var(--accent)"/>
    </svg>
    <span class="band-url">buildlinkhub.example</span>
  </section>

  <section class="card card-back" aria-label="Business card back">
    <div class="back-brand">
      <div class="back-brand-name">BuildLinkHub.com</div>
      <div class="back-brand-url">www.buildlinkhub.example</div>
    </div>
  </section>
</body>
</html>
```